Corvane Freight Company Business Card Design

We are a company that delivers natural saltwater (from the ocean) to aquarium companies, restaurants and home marine tanks. I would like a new business card to suit.

Must include Name, company name, abn, contact number and website as well as logo (see attached).

Looking for a design that stands out, has a clean but unique appearance.

Double and single sided entries welcome

Business

• Logo

```html
<!DOCTYPE html>
<html lang="en">
<head>
<meta charset="utf-8">
<title>Corvane Freight Company – Business Card</title>
<link href="https://fonts.googleapis.com/css2?family=Open+Sans:wght@400;600;700&display=swap" rel="stylesheet">
<style>
  :root {
    --backdrop: #1c1c1e;
    --card-blue: #3172ee;
    --wave-light: #45aaf6;
    --wave-pale: #8fd3fb;
    --text-white: #ffffff;
  }
  * { margin: 0; padding: 0; box-sizing: border-box; }
  html, body {
    width: 1200px; height: 405px; overflow: hidden;
    background: var(--backdrop);
    font-family: "Open Sans", Arial, sans-serif;
    color: var(--text-white);
  }
  .stage { position: relative; width: 1200px; height: 405px; }
  .card {
    position: absolute; top: 48px; width: 525px; height: 300px;
    background: var(--card-blue); overflow: hidden;
  }
  .card--front { left: 50px; }
  .card--back { left: 617px; }
  .card__wave-area {
    position: absolute; left: 0; right: 0; bottom: 0; height: 150px;
    background: linear-gradient(168deg, rgba(69,170,246,0) 30%, var(--wave-light) 62%, var(--wave-pale) 100%);
  }
  .brand {
    position: absolute; display: flex; align-items: center; gap: 12px;
    white-space: nowrap;
  }
  .brand__dot {
    width: 34px; height: 34px; border-radius: 50%;
    background: var(--wave-pale); flex: none;
  }
  .brand__name { font-weight: 700; font-size: 34px; letter-spacing: -0.5px; line-height: 40px; }
  .card--front .brand { left: 40px; top: 72px; }
  .card--back .brand { left: 0; right: 0; top: 112px; justify-content: center; }
  .holder { position: absolute; right: 27px; top: 32px; text-align: right; }
  .holder__name { font-weight: 700; font-size: 22px; line-height: 28px; }
  .holder__title { font-size: 16px; line-height: 24px; }
  .address {
    position: absolute; left: 79px; top: 183px; font-style: normal;
    font-size: 12.5px; line-height: 19px;
  }
  .address__company { font-weight: 700; }
  .contacts {
    position: absolute; right: 27px; top: 219px; text-align: right;
    font-size: 13.5px; line-height: 22px;
  }
  .contacts li { list-style: none; display: flex; justify-content: flex-end; align-items: center; gap: 5px; }
  .contacts svg { width: 12px; height: 12px; }
  .back-web {
    position: absolute; left: 0; right: 0; top: 238px; text-align: center;
    font-size: 15.5px; letter-spacing: 3px;
  }
</style>
</head>
<body>
<main class="stage">
  <section class="card card--front">
    <div class="card__wave-area" role="img" aria-label="Soft ocean wave decoration in light blue"></div>
    <div class="brand">
      <span class="brand__dot"></span>
      <span class="brand__name">Corvane Freight</span>
    </div>
    <div class="holder">
      <div class="holder__name">Your name</div>
      <div class="holder__title">Title</div>
    </div>
    <address class="address">
      <div class="address__company">Corvane Freight Company</div>
      <div>Street Name, City Name</div>
      <div>State, City Zip Code</div>
    </address>
    <ul class="contacts">
      <li><svg viewBox="0 0 12 12"><path d="M3,1 L5,3.5 L4,5 C4.6,6.4 5.6,7.4 7,8 L8.5,7 L11,9 L9.5,11 C5,10.5 1.5,7 1,2.5 Z" fill="none" stroke="#fff" stroke-width="1"/></svg>123-456-7890</li>
      <li><svg viewBox="0 0 12 12"><circle cx="6" cy="6" r="5.5" fill="#fff"/><path d="M0.5,6 H11.5 M6,0.5 C3,3 3,9 6,11.5 M6,0.5 C9,3 9,9 6,11.5" stroke="var(--card-blue)" stroke-width="0.8" fill="none"/></svg>www.website.com</li>
      <li>ABN : 0123456789</li>
    </ul>
  </section>

  <section class="card card--back">
    <div class="brand">
      <span class="brand__dot"></span>
      <span class="brand__name">Corvane Freight</span>
    </div>
    <div class="back-web">www.website.com</div>
  </section>
</main>
</body>
</html>
```